Business card design/logo/website name

I am a business coach. My business name is KDP (Kessel Dunmore & Partners, Inc.) I want to use this card just for coaching. I do two kinds: Personal Image coach and Executive business coach
1. I work with people to become a polished global professional.
"Become a confident, savvy professional building relationships tactfully and appropriately while clearly representing your own company’s message and image.
Learn the nuances… Master the skills… Use the business etiquette techniques and protocols that allow you to seamlessly and confidently conduct business in a global business environment.
Have the comfort of knowing what to expect, what to do and how to easily build long and short-term relationships that give you the winning edge and increased company profits."
2. Leadership Coaching
For increasing the team’s productivity by building stronger relationships. Build strong compelling vision and write and share their Personal Leadership Philosophy, a roadmap that is concise and commanding and gives the team a clear vision of the leader's expectations.
Updates

KDP should be the logo. (Downplay the Kessel Dunmore and Partners, Inc.)

Want:
Executive Coach
Consultant

Reason: I am traveling and connections are often broken.

Target Market(s)

Executives, business people

Industry/Entity Type

Building

Font styles to use
Sans Serif
Script

Colors
0255a3
3176b5
85acd3
ec2027

Requirements
Must have
• KDP as the logo,(no preference on how you treat KDP) with Kessel Dunmore & Partners. Inc. downplayed.
On the card:
Rosalind Dunmore CEO
Executive Coach
Consultant
KRC 4(c)
Coaching - Training - Strategic Planning

```html
<!DOCTYPE html>
<html lang="en">
<head>
<meta charset="utf-8">
<title>KDP — Kessel Dunmore &amp; Partners — Business Card</title>
<link rel="stylesheet" href="https://fonts.googleapis.com/css2?family=Michroma&family=Exo+2:wght@400;500&display=swap">
<style>
  :root {
    --page-bg: #e6e4e0;
    --card-white: #f8f8f8;
    --card-shade: #e8e9eb;
    --brand-navy: #0255a3;
    --brand-blue: #3176b5;
    --brand-sky: #85acd3;
    --brand-red: #ec2027;
    --ink-grey: #3a3a3a;
    --text-light: #ffffff;
  }
  * { margin: 0; padding: 0; box-sizing: border-box; }
  html, body {
    width: 1200px;
    height: 1085px;
    overflow: hidden;
    background: var(--page-bg);
  }
  .business-card {
    position: absolute;
    left: 75px;
    top: 242px;
    width: 1050px;
    height: 600px;
    background: linear-gradient(120deg, var(--card-white) 40%, var(--card-shade) 100%);
    box-shadow: 0 14px 30px rgba(0,0,0,0.22);
    overflow: hidden;
  }
  .contact-panel {
    position: absolute;
    left: 0;
    top: 0;
    width: 1050px;
    height: 600px;
  }
  .contact-group {
    position: absolute;
    text-align: right;
    color: var(--text-light);
    font-family: "Exo 2", sans-serif;
    font-size: 25px;
    line-height: 36px;
    letter-spacing: 0.5px;
    white-space: nowrap;
  }
  .contact-phone   { right: 666px; top: 94px; }
  .contact-address { right: 656px; top: 226px; }
  .contact-web     { right: 646px; top: 394px; }

  .identity {
    position: absolute;
    left: 580px;
    top: 64px;
    width: 430px;
  }
  .logo {
    display: flex;
    align-items: center;
    gap: 18px;
  }
  .logo-mark {
    font-family: "Michroma", sans-serif;
    font-size: 62px;
    line-height: 76px;
    letter-spacing: 6px;
    color: var(--brand-navy);
  }
  .logo-dot {
    width: 18px;
    height: 18px;
    border-radius: 50%;
    background: var(--brand-red);
  }
  .company-name {
    margin-top: 6px;
    font-family: "Exo 2", sans-serif;
    font-weight: 400;
    font-size: 18px;
    line-height: 24px;
    letter-spacing: 1.5px;
    color: var(--brand-blue);
  }
  .divider {
    margin: 34px 0 30px;
    width: 120px;
    height: 3px;
    background: var(--brand-sky);
  }
  .person-name {
    font-family: "Michroma", sans-serif;
    font-size: 24px;
    line-height: 34px;
    letter-spacing: 1px;
    text-transform: uppercase;
    color: var(--ink-grey);
  }
  .person-title {
    margin-top: 8px;
    font-family: "Exo 2", sans-serif;
    font-weight: 500;
    font-size: 22px;
    line-height: 30px;
    color: var(--brand-navy);
  }
  .person-roles {
    font-family: "Exo 2", sans-serif;
    font-size: 22px;
    line-height: 30px;
    color: var(--ink-grey);
  }
  .credential {
    margin-top: 26px;
    font-family: "Exo 2", sans-serif;
    font-weight: 500;
    font-size: 18px;
    line-height: 24px;
    letter-spacing: 1px;
    color: var(--brand-red);
  }
  .services {
    margin-top: 4px;
    font-family: "Exo 2", sans-serif;
    font-size: 19px;
    line-height: 26px;
    color: var(--brand-blue);
  }
</style>
</head>
<body>
  <div class="business-card">
    <svg class="contact-panel" viewBox="0 0 1050 600" aria-hidden="true">
      <g fill="var(--brand-navy)">
        <polygon points="0,0 440,0 480,600 0,600"/>
        <circle cx="452" cy="130" r="44"/>
        <circle cx="462" cy="280" r="44"/>
        <circle cx="472" cy="430" r="44"/>
      </g>
      <g fill="none" stroke="var(--text-light)" stroke-width="3">
        <circle class="icon-ring" cx="452" cy="130" r="27"/>
        <circle class="icon-ring" cx="462" cy="280" r="27"/>
        <circle class="icon-ring" cx="472" cy="430" r="27"/>
      </g>
      <path class="icon-phone" fill="var(--text-light)"
            d="M441,116 q4,-3 7,1 l3,6 q1,3 -2,5 l-3,2 q2,6 9,11 l2,-3 q2,-3 5,-2 l6,3 q4,3 1,7 l-3,3 q-4,3 -10,0 q-12,-7 -18,-19 q-3,-7 0,-11 z"/>
      <path class="icon-pin" fill="var(--text-light)" fill-rule="evenodd"
            d="M462,265 a11,11 0 0 1 11,11 c0,8 -11,20 -11,20 c0,0 -11,-12 -11,-20 a11,11 0 0 1 11,-11 z M462,271 a5,5 0 1 0 0.01,0 z"/>
      <g class="icon-globe" fill="none" stroke="var(--text-light)" stroke-width="2.2">
        <circle cx="472" cy="430" r="14"/>
        <ellipse cx="472" cy="430" rx="6" ry="14"/>
        <line x1="458" y1="430" x2="486" y2="430"/>
        <line x1="460" y1="423" x2="484" y2="423"/>
        <line x1="460" y1="437" x2="484" y2="437"/>
      </g>
    </svg>

    <div class="contact-group contact-phone">014 278 5390<br>014 278 5390</div>
    <div class="contact-group contact-address">041.12th floor,<br>Harbor Line Road<br>BRK</div>
    <div class="contact-group contact-web">rdunmore@kdpmail.com<br>kdpcoaching.com</div>

    <div class="identity">
      <div class="logo">
        <span class="logo-mark">KDP</span>
        <span class="logo-dot"></span>
      </div>
      <h1 class="company-name">Kessel Dunmore &amp; Partners, Inc.</h1>
      <div class="divider"></div>
      <p class="person-name">Rosalind Dunmore</p>
      <p class="person-title">CEO</p>
      <p class="person-roles">Executive Coach | Consultant</p>
      <p class="credential">KRC 4(c)</p>
      <p class="services">Coaching - Training - Strategic Planning</p>
    </div>
  </div>
</body>
</html>
```